Brightway Haus Inc. Business Card Design

Brightway Haus Inc. is in search of a great clean design for our business cards!

Looking to incorporate our full logo and watermark on side one (however, I am open to having the text and watermark separated within the design.)

On side two, I am looking to have contact information (Name, Position, Phone #, Email, Website (www.thebrightwayhaus.ca). Can have the logo and/or watermark as part of the design if applicable.

Please add tagline "Where Shine Counts" on either side 1 or 2. This tagline can be in a sans serif, serif or cursive font as long as it compliments overall design. Capitalization can be title or sentence case depending on how it fits within the design.

Get creative!! Looking for a clean, crisp, premium design! Looking for a glossy card finish with spot UV features when printed. Cards will also be printed with rounded corners. Standard dimensions (3.5 x 2).

Target Market(s)

B2B - primary clients are business owners or property management corporations. (residential jobs are few and far between)

Industry/Entity Type

Business

Contact Information for Business Card

- clean, crisp design
- double sided
- spot UV accents and glossy finish upon printing
- standard business card size (3.5 x 2) with rounded corners
- please see project description for requirements per side

Font styles to use
Sans Serif

Requirements
Must have
• - adequate bleeds with print ready files
• - cohesive design elements between side 1 & 2
• - spot UV elements (can be on both sides or just one, use your discretion)
• - colour pallet should match the logo file provided
• - incorporate tagline "where shine counts" (this tagline can be in a serif or sans serif font as long as it is complimentary to the overall design.
Nice to have
• - Premium elements with a clean design
Should not have
• - Please omit cartoon or whimsical like designs, think premium.
• - Colours should not stray from the pallet of the provided logo.

```html
<!DOCTYPE html>
<html lang="en">
<head>
<meta charset="utf-8">
<title>Brightway Haus Inc. Business Card</title>
<link href="https://fonts.googleapis.com/css2?family=Roboto:ital,wght@0,400;0,500;0,700;1,400&display=swap" rel="stylesheet">
<style>
  :root {
    --backdrop: #2b2b2b;
    --teal: #10b8ba;
    --navy: #1f2455;
    --white: #ffffff;
    --paper: #f1f1f1;
    --rule: #2a3470;
  }
  * { margin: 0; padding: 0; box-sizing: border-box; }
  html, body { width: 1200px; height: 960px; overflow: hidden; }
  body {
    background: var(--backdrop);
    font-family: "Roboto", Arial, sans-serif;
    position: relative;
  }
  .card {
    position: absolute;
    width: 600px;
    height: 343px;
    overflow: hidden;
  }
  .card-front { left: 314px; top: 113px; background: var(--white); }
  .card-back { left: 311px; top: 472px; background: var(--paper); }

  .front-panel { position: absolute; inset: 0; }

  .front-brand {
    position: absolute;
    left: 44px;
    top: 60px;
    color: var(--white);
    font-weight: 700;
    font-size: 27px;
    letter-spacing: -0.3px;
  }
  .front-address {
    position: absolute;
    left: 45px;
    top: 162px;
    color: var(--white);
    font-size: 14.5px;
    line-height: 18px;
  }
  .contact-list {
    position: absolute;
    left: 43px;
    top: 211px;
    list-style: none;
    color: var(--white);
    font-size: 14.5px;
  }
  .contact-list li {
    display: flex;
    align-items: center;
    height: 19.3px;
  }
  .contact-list svg { width: 14px; height: 14px; margin-right: 8px; fill: var(--white); }

  .holder {
    position: absolute;
    left: 400px;
    top: 168px;
    width: 155px;
    text-align: center;
    color: var(--teal);
  }
  .holder-name { font-weight: 500; font-size: 20px; }
  .holder-role { font-weight: 500; font-size: 14.5px; margin-top: 3px; }

  .back-brand {
    position: absolute;
    left: 0;
    right: 0;
    top: 140px;
    text-align: center;
    color: var(--navy);
    font-weight: 700;
    font-size: 46px;
    letter-spacing: -1px;
  }
  .tagline {
    position: absolute;
    left: 0;
    right: 0;
    top: 276px;
    display: flex;
    align-items: center;
    justify-content: center;
    gap: 4px;
    color: var(--navy);
    font-style: italic;
    font-size: 19px;
  }
  .tagline-accent { color: var(--teal); }
  .tagline-rule {
    width: 112px;
    height: 1px;
  }
  .tagline-rule.left { background: linear-gradient(to right, transparent, var(--rule)); }
  .tagline-rule.right { background: linear-gradient(to left, transparent, var(--rule)); }
</style>
</head>
<body>
  <section class="card card-front">
    <svg class="front-panel" viewBox="0 0 600 343" aria-hidden="true">
      <polygon points="0,0 340,0 258,343 0,343" fill="var(--teal)"/>
    </svg>
    <div class="front-brand">BRIGHTWAY HAUS INC.</div>
    <address class="front-address" style="font-style:normal">
      4120 Larkspur Road<br>Fairbanks, Alaska 34810
    </address>
    <ul class="contact-list">
      <li><svg viewBox="0 0 16 16"><path d="M3.5 1l2.5 3-1.5 1.8c.9 2 2.6 3.7 4.7 4.7L11 9l3 2.5-1.6 2.6C7 14 2 9 1.9 3.1z"/></svg>555 214 0187</li>
      <li><svg viewBox="0 0 16 16"><path d="M4.5 1h7v14h-7zM6 2.5v9.5h4V2.5zM7.4 13h1.2v1H7.4z" fill-rule="evenodd"/></svg>555 302 7741</li>
      <li><svg viewBox="0 0 16 16"><path d="M4 1h8v4H4zM1 6h14v6h-2v3H3v-3H1zM4.5 10v3.5h7V10z" fill-rule="evenodd"/></svg>555 418 3360</li>
      <li><svg viewBox="0 0 16 16"><path d="M1 4h14v9H1zM2 5l6 4.5L14 5v1.3L8 10.8 2 6.3z" fill-rule="evenodd"/></svg>hello@brightwayhaus.ca</li>
      <li><svg viewBox="0 0 16 16"><circle cx="8" cy="8" r="6.5"/></svg>www.thebrightwayhaus.ca</li>
    </ul>
    <div class="holder">
      <div class="holder-name">DANIEL REYES</div>
      <div class="holder-role">CEO/FOUNDER</div>
    </div>
  </section>

  <section class="card card-back">
    <div class="back-brand">BRIGHTWAY HAUS INC.</div>
    <div class="tagline">
      <span class="tagline-rule left"></span>
      <span>Where <span class="tagline-accent">Shine</span> Counts</span>
      <span class="tagline-rule right"></span>
    </div>
  </section>
</body>
</html>
```